Postcard design to acquire new clients for my Property Management Company

I'm looking for a postcard design that I can send to prospective clients detailing information about my company and services.
Postcard should be eye catching and contain information from www.bramblecrestpm.com. I've provided a few screen shots for the most important information and my logo.
Target Market(s)
Real Estate
Industry/Entity Type
Real Estate
Font styles to use
Sans Serif
Requirements
Must have
- Must be eye catching!! this will be a direct mail piece - I'd like for the card to be read and not tossed in the trash immediately.
Design que from the logo.
A place to write / print the receipts name and address.
our physical address - 2387 Hollow Pine Road, Lubbock, TX 79852.
Should not have
- the contact information on the business card is not accurate - please use info from website.

```html
<!DOCTYPE html>
<html lang="en">
<head>
<meta charset="utf-8">
<title>Bramblecrest Property Management – Postcard</title>
<link rel="stylesheet" href="https://fonts.googleapis.com/css2?family=Montserrat:wght@400;500;600;700;800;900&family=Open+Sans:wght@600;700;800&display=swap">
<style>
  :root {
    --brand-blue: #124f8a;
    --charcoal: #333335;
    --ink: #111111;
    --muted-text: #4a4a4a;
    --paper: #ffffff;
    --mail-grey: #c4c4c5;
    --page-bg: #e9eaec;
    --label: #555a60;
  }
  * { box-sizing: border-box; margin: 0; padding: 0; }
  html, body { width: 1200px; height: 900px; overflow: hidden; }
  body {
    background: var(--page-bg);
    font-family: "Montserrat", Arial, sans-serif;
    position: relative;
  }
  .side-label {
    position: absolute; top: 212px;
    font-size: 22px; font-weight: 500; color: var(--label);
  }
  .card-slot {
    position: absolute; top: 262px;
    width: 560px; height: 397px;
    box-shadow: 0 6px 18px rgba(0,0,0,.18);
  }
  .card-slot.front-slot { left: 25px; }
  .card-slot.back-slot { left: 615px; }
  .card {
    position: absolute; left: 0; top: 0;
    width: 1000px; height: 708px;
    transform: scale(0.56); transform-origin: 0 0;
    overflow: hidden;
  }
  .card-shapes { position: absolute; inset: 0; width: 1000px; height: 708px; }

  /* FRONT */
  .brand-name {
    position: absolute; right: 25px; top: 14px; text-align: right;
    color: var(--brand-blue); font-weight: 600;
  }
  .brand-name .brand-main { display: block; font-size: 50px; letter-spacing: 7px; line-height: 1.05; }
  .brand-name .brand-sub { display: block; font-size: 24px; letter-spacing: 5.5px; line-height: 1.2; }
  .headline { position: absolute; right: 25px; top: 160px; text-align: right; }
  .headline span { display: block; line-height: 1; }
  .headline .hl-property { font-size: 94px; font-weight: 900; color: var(--ink); letter-spacing: -1px; }
  .headline .hl-management { font-size: 66px; font-weight: 700; color: var(--brand-blue); margin-top: 10px; }
  .headline .hl-city { font-size: 54px; font-weight: 700; color: var(--ink); margin-top: 12px; letter-spacing: -0.5px; }
  .accent-rule {
    position: absolute; left: 905px; top: 404px; width: 95px; height: 4px;
    background: var(--brand-blue);
  }
  .tagline {
    position: absolute; right: 25px; top: 428px; text-align: right;
    font-size: 25px; font-weight: 500; color: var(--muted-text); line-height: 1.22;
  }
  .contact-heading {
    position: absolute; right: 25px; top: 558px;
    font-family: "Open Sans", Arial, sans-serif;
    font-size: 28px; font-weight: 700; color: var(--paper);
  }
  .contact-list { position: absolute; right: 20px; top: 600px; list-style: none; }
  .contact-list li {
    display: flex; justify-content: flex-end; align-items: center;
    font-size: 29px; color: var(--paper); line-height: 1.12;
  }
  .contact-list svg { width: 28px; height: 28px; margin-left: 16px; flex: none; }

  /* BACK */
  .services-title {
    position: absolute; left: 0; top: 18px; width: 500px; height: 42px;
    font-family: "Open Sans", Arial, sans-serif;
    font-size: 30px; font-weight: 800; color: var(--paper);
    display: flex; align-items: center; justify-content: center;
    padding-right: 10px;
  }
  .service { position: absolute; width: 270px; }
  .service .service-icon {
    position: absolute; left: -54px; top: 0; width: 42px; height: 42px;
    fill: var(--brand-blue);
  }
  .service h3 {
    font-family: "Open Sans", Arial, sans-serif;
    font-size: 23px; font-weight: 600; color: var(--brand-blue);
    line-height: 1.2; white-space: nowrap;
  }
  .service p {
    font-size: 14px; font-weight: 500; color: var(--ink);
    line-height: 1.1; margin-top: 4px; letter-spacing: -0.2px;
  }
  .stamp-box {
    position: absolute; left: 822px; top: 20px; width: 138px; height: 158px;
    border: 2px solid #2c2c2c;
  }
  .address-line {
    position: absolute; left: 622px; width: 340px; height: 2px; background: #2c2c2c;
  }
  .closing-line {
    position: absolute; left: 0; top: 585px; width: 590px; text-align: center;
    font-size: 31px; font-weight: 500; color: var(--paper); line-height: 1.3;
  }
  .return-address {
    position: absolute; left: 620px; top: 628px; width: 370px; text-align: center;
    font-size: 17px; font-weight: 600; color: var(--brand-blue);
  }
</style>
</head>
<body>

<span class="side-label" style="left:52px;">Front</span>
<span class="side-label" style="left:640px;">Back</span>

<!-- FRONT -->
<div class="card-slot front-slot">
  <section class="card card-front">
    <svg class="card-shapes" viewBox="0 0 1000 708" aria-hidden="true">
      <rect width="1000" height="708" fill="var(--charcoal)"/>
      <polygon points="484,0 1000,0 1000,595 398,595 518,335 405,135" fill="var(--paper)"/>
      <polygon points="750,557 1000,557 1000,595 735,595" fill="var(--charcoal)"/>
      <polygon points="410,595 1000,595 1000,708 478,708" fill="var(--brand-blue)"/>
      <polyline points="348,42 518,335 348,672" fill="none" stroke="var(--brand-blue)" stroke-width="4"/>
    </svg>
    <svg class="card-shapes" viewBox="0 0 1000 708" role="img" aria-label="Photo of a small model house with a red and white facade and grey roof beside a set of house keys on a wooden table">
      <defs>
        <linearGradient id="photoTone" x1="0" y1="0" x2="1" y2="1">
          <stop offset="0" stop-color="#7b8088"/>
          <stop offset="0.5" stop-color="#a8403a"/>
          <stop offset="1" stop-color="#9a6a3a"/>
        </linearGradient>
      </defs>
      <polygon points="0,42 348,42 518,335 348,672 0,672" fill="url(#photoTone)"/>
    </svg>

    <div class="brand-name">
      <span class="brand-main">BRAMBLECREST</span>
      <span class="brand-sub">PROPERTY MANAGEMENT</span>
    </div>

    <h1 class="headline">
      <span class="hl-property">PROPERTY</span>
      <span class="hl-management">MANAGEMENT</span>
      <span class="hl-city">ACROSS LUBBOCK</span>
    </h1>
    <div class="accent-rule"></div>
    <p class="tagline">Maximize your financial returns with<br>support from our rental specialists</p>

    <p class="contact-heading">Contact us:</p>
    <ul class="contact-list">
      <li>(806) 555-0147
        <svg viewBox="0 0 24 24" aria-hidden="true"><path fill="#fff" d="M6.6 10.8a15.1 15.1 0 0 0 6.6 6.6l2.2-2.2c.3-.3.7-.4 1-.2 1.1.4 2.3.6 3.6.6.6 0 1 .4 1 1V20c0 .6-.4 1-1 1C10.6 21 3 13.4 3 4c0-.6.4-1 1-1h3.5c.6 0 1 .4 1 1 0 1.3.2 2.5.6 3.6.1.3 0 .7-.2 1z"/></svg>
      </li>
      <li>info@bramblecrestpm.com
        <svg viewBox="0 0 24 24" aria-hidden="true"><rect x="2" y="5" width="20" height="14" fill="none" stroke="#fff" stroke-width="1.8"/><path d="M2 5l10 8 10-8M2 19l7.5-7M22 19l-7.5-7" fill="none" stroke="#fff" stroke-width="1.6"/></svg>
      </li>
      <li>bramblecrestpm.com
        <svg viewBox="0 0 24 24" aria-hidden="true"><g fill="none" stroke="#fff" stroke-width="1.5"><circle cx="12" cy="12" r="9"/><ellipse cx="12" cy="12" rx="4" ry="9"/><path d="M3 12h18M5 7h14M5 17h14"/></g></svg>
      </li>
    </ul>
  </section>
</div>

<!-- BACK -->
<div class="card-slot back-slot">
  <section class="card card-back">
    <svg class="card-shapes" viewBox="0 0 1000 708" aria-hidden="true">
      <rect width="1000" height="708" fill="var(--paper)"/>
      <rect x="590" y="0" width="410" height="708" fill="var(--mail-grey)"/>
      <polygon points="0,18 475,18 502,60 0,60" fill="var(--brand-blue)"/>
      <polygon points="0,562 592,562 618,620 600,665 655,708 0,708" fill="var(--brand-blue)"/>
      <polygon points="618,620 1000,620 1000,665 600,665" fill="var(--paper)"/>
    </svg>

    <h2 class="services-title">OUR SERVICES</h2>

    <div class="service" style="left:66px; top:86px;">
      <svg class="service-icon" viewBox="0 0 24 24" aria-hidden="true"><path d="M12 3 1 12.5l1.4 1.5L4 12.6V21h6v-5h4v5h6v-8.4l1.6 1.4 1.4-1.5z"/></svg>
      <h3>Property Marketing</h3>
      <p>Let us take over your marketing<br>for you and we'll find a quali-<br>fied renter quickly.</p>
    </div>

    <div class="service" style="left:66px; top:187px;">
      <svg class="service-icon" viewBox="0 0 24 24" aria-hidden="true"><circle cx="8" cy="7" r="3.5"/><circle cx="17" cy="7" r="3.2"/><path d="M1 20c0-4.5 3-7 7-7s7 2.5 7 7zM14 20c0-2.7-.8-4.8-2.3-6.2 1.3-.6 3-.8 5.3-.8 3.8 0 6 2.3 6 7z"/></svg>
      <h3>Tenant Screening</h3>
      <p>We don't just find someone to<br>rent your home—we find the<br>best renters. We screen all ap-<br>plications using fair housing<br>guidelines to protect you.</p>
    </div>

    <div class="service" style="left:64px; top:301px;">
      <svg class="service-icon" viewBox="0 0 24 24" aria-hidden="true"><text x="12" y="21" text-anchor="middle" font-family="Montserrat, sans-serif" font-size="24" font-weight="700">$</text></svg>
      <h3>Rent Collection</h3>
      <p>Stop guessing when you'll re-<br>ceive your rental earnings every<br>month and say hello to consis-<br>tent payments. We keep your<br>tenants current.</p>
    </div>

    <div class="service" style="left:63px; top:421px;">
      <svg class="service-icon" viewBox="0 0 24 24" aria-hidden="true"><path d="M13 3l8 8-2.5 2.5-2-2L5 23l-3-3L13.5 8.5l-2-2z"/></svg>
      <h3>Maintenance</h3>
      <p>Still scrambling to respond to<br>repair requests every time you<br>receive a tenant call? Let us co-<br>ordinate repair work on your<br>behalf!</p>
    </div>

    <div class="service" style="left:340px; top:82px;">
      <svg class="service-icon" viewBox="0 0 24 24" aria-hidden="true"><path d="M10 2a8 8 0 0 1 6.4 12.8l5.9 5.9-2 2-5.9-5.9A8 8 0 1 1 10 2zm0 3a5 5 0 1 0 0 10 5 5 0 0 0 0-10z"/></svg>
      <h3>Property Inspections</h3>
      <p>We visit every home in our<br>portfolio regularly.</p>
    </div>

    <div class="service" style="left:340px; top:167px;">
      <svg class="service-icon" viewBox="0 0 24 24" aria-hidden="true"><path d="M2 2h2v18h18v2H2z"/><rect x="7" y="12" width="2" height="6"/><rect x="11" y="8" width="2" height="10"/><rect x="15" y="10" width="2" height="8"/><rect x="19" y="6" width="2" height="12"/></svg>
      <h3>Financial Reporting</h3>
      <p>Keep a handle on your real<br>estate performance. We generate<br>monthly statements so you can<br>review income &amp; expenses at a<br>moment's notice.</p>
    </div>

    <div class="service" style="left:339px; top:290px;">
      <svg class="service-icon" viewBox="0 0 24 24" aria-hidden="true"><path d="M12 1 3 4.5V11c0 6 4 10.5 9 12 5-1.5 9-6 9-12V4.5zm0 2.4V20.7c-3.7-1.4-6.5-5-6.5-9.7V6.2z"/></svg>
      <h3>Evictions</h3>
      <p>When things go wrong inside<br>your rental home, rest easy with<br>the experts on your side. We will<br>handle evictions for you &amp; find<br>new renters when its over.</p>
    </div>

    <div class="service" style="left:339px; top:415px;">
      <svg class="service-icon" viewBox="0 0 24 24" aria-hidden="true"><path d="M11 2h2v3h7v2h-1.2L22 14a4 4 0 0 1-7 0l3.2-7H13v13h4v2H7v-2h4V7H5.8L9 14a4 4 0 0 1-7 0l3.2-7H4V5h7zM5.5 8.6 3.3 13.5h4.4zm13 0-2.2 4.9h4.4z"/></svg>
      <h3>Legal Guidance</h3>
      <p>Don't accidentally violate one of<br>the many ordinances and hous-<br>ing laws governing your relation-<br>ship with your tenants. Let us<br>keep you compliant.</p>
    </div>

    <div class="stamp-box" aria-hidden="true"></div>
    <div class="address-line" style="top:257px;"></div>
    <div class="address-line" style="top:361px;"></div>
    <div class="address-line" style="top:466px;"></div>

    <p class="closing-line">CHOOSE THE RIGHT<br>PROPERTY MANAGEMENT SYSTEM</p>
    <p class="return-address">2387 Hollow Pine Road, Lubbock, TX 79852</p>
  </section>
</div>

</body>
</html>
```